Elegant Business Card for Technology Company

Client is a supplier of innovative industrial communications and automation equipment since 2002. This contest is to gather fresh ideas for a redesign of the existing business card. Client is looking for design that best communicates tagline "Industrial Networking and Computing Specialist".

Design submissions should look modern, clean, elegant and professional. It should not be cluttered. Use white as the primary colour. Orange and black as secondary colour. Refer to jpeg File 1 on the current design.

Fonts used by Client used include Arial Regular, Arial Black, Roboto Regular, Roboto Black and Lato.

The winning design will be sent for offset printing using super white 250gsm artcard paper (open for suggestions).

Target Market(s)

System Engineers, Project Managers, Purchasing Managers from companies providing engineering services for Smart Cities.

Industry/Entity Type

Information Technology

Contact Information for Business Card

Refer to PDF File 3 for Business Card Details. Priority of short contact information would be as follows Name > Job Title > Email > Mobile > Web > Tel > Fax > Business Address >UEN (UEN represents company registration number)

Font styles to use
Sans Serif

Colors
ffffff
f37122
000000
5c5c5c

Requirements
Must have
• Refer to AI File 2 (Company Logo) & PDF File 3 (Information on Namecard)
Should not have
• No QR codes
• No Social Media Icons
• Do not create full Black or Orange colour background

```html
<!DOCTYPE html>
<html lang="en">
<head>
<meta charset="utf-8">
<title>Kestrel Asia Pacific – Business Card</title>
<link href="https://fonts.googleapis.com/css2?family=Lato:wght@400;700;900&display=swap" rel="stylesheet">
<style>
  :root{
    --white:#ffffff;
    --orange:#f37122;
    --black:#000000;
    --grey:#5c5c5c;
    --band-grey:#4a4a50;
    --stage:#262626;
    --map-tone:#e6e6e6;
    --map-warm:#f6e3da;
  }
  *{box-sizing:border-box;margin:0;padding:0}
  html,body{width:1200px;height:873px;overflow:hidden}
  body{background:var(--stage);font-family:'Lato',Arial,sans-serif;position:relative}

  .card{position:absolute;width:540px;height:310px;background:var(--white);overflow:hidden;
        box-shadow:0 12px 30px rgba(0,0,0,.5)}
  .card--back{left:50px;top:70px}
  .card--front{left:610px;top:490px}

  .card__bands{position:absolute;left:0;bottom:0;width:540px;height:40px}

  .world-map{position:absolute;border-radius:40% 50% 45% 40%;
             background:radial-gradient(ellipse at 40% 50%,var(--map-warm),var(--map-tone) 55%,rgba(230,230,230,0) 75%);
             opacity:.8}
  .card--back .world-map{left:110px;top:60px;width:330px;height:190px}
  .card--front .world-map{left:110px;top:40px;width:380px;height:210px}

  .brand{position:absolute;display:flex;align-items:center;gap:10px}
  .brand__dot{width:40px;height:40px;border-radius:50%;background:var(--orange);flex:none}
  .brand__text{display:flex;flex-direction:column;color:var(--black);font-weight:900;line-height:1}
  .brand__name{font-size:28px;letter-spacing:1px}
  .brand__legal{font-size:10.5px;letter-spacing:.3px;margin-top:4px}
  .card--back .brand{left:175px;top:40px}
  .card--front .brand{left:285px;top:105px}
  .card--front .brand__dot{width:52px;height:52px}
  .card--front .brand__name{font-size:34px}
  .card--front .brand__legal{font-size:12px}

  .services{position:absolute;left:70px;top:118px;list-style:none;display:grid;
            grid-template-columns:auto auto;column-gap:22px;row-gap:9px;
            font-size:12.5px;color:var(--grey)}
  .services li{position:relative;padding-left:11px}
  .services li::before{content:"";position:absolute;left:0;top:6px;width:5px;height:5px;border-radius:50%;background:var(--orange)}
  .services li.wide{grid-column:1 / span 2;justify-self:center}

  .tagline{position:absolute;left:0;right:0;top:220px;text-align:center;
           font-size:17px;font-weight:700;color:var(--orange)}

  .person{position:absolute;left:28px;top:28px}
  .person__name{font-size:19px;font-weight:900;color:var(--black)}
  .person__title{font-size:12px;color:var(--black);margin-top:3px}

  .contacts{position:absolute;left:28px;top:104px;list-style:none;font-size:14px;font-weight:700;color:var(--black)}
  .contacts li{display:flex;align-items:center;gap:12px;height:27px}
  .contacts svg{width:15px;height:15px;flex:none;fill:var(--grey);stroke:var(--grey)}

  .uen{position:absolute;right:24px;top:234px;font-size:11.5px;color:var(--black)}
</style>
</head>
<body>

<section class="card card--back" aria-label="Business card back">
  <div class="world-map" role="img" aria-label="Faint dotted world map"></div>
  <div class="brand">
    <span class="brand__dot"></span>
    <span class="brand__text"><span class="brand__name">KESTREL</span><span class="brand__legal">KESTREL ASIA PACIFIC PTE LTD</span></span>
  </div>
  <ul class="services">
    <li>Remote Automation</li>
    <li>IP Video Surveillance</li>
    <li>Serial / Fieldbus Connectivity</li>
    <li>Industrial &amp; Embedded Computing</li>
    <li class="wide">Industrial Ethernet / Wireless / Cellular</li>
  </ul>
  <p class="tagline">Industrial Networking and Computing Specialist</p>
  <svg class="card__bands" viewBox="0 0 540 40" aria-hidden="true">
    <rect x="0" y="28" width="540" height="12" fill="var(--band-grey)"/>
    <path d="M360 40 Q364 20 384 20 L540 20 L540 40 Z" fill="var(--orange)"/>
  </svg>
</section>

<section class="card card--front" aria-label="Business card front">
  <div class="world-map" role="img" aria-label="Faint dotted world map"></div>
  <div class="person">
    <p class="person__name">Daniel Koh</p>
    <p class="person__title">Sales Manager</p>
  </div>
  <ul class="contacts">
    <li><svg viewBox="0 0 16 16"><rect x="1" y="3" width="14" height="10" stroke-width="0"/><path d="M1 3 L8 9 L15 3" fill="none" stroke="#fff" stroke-width="1.3"/></svg>sales@kestrel.com.sg</li>
    <li><svg viewBox="0 0 16 16"><rect x="4" y="1" width="8" height="14" rx="1.5" fill="none" stroke-width="1.5"/></svg>+65 6123 4501</li>
    <li><svg viewBox="0 0 16 16"><path d="M6 10 L10 6 M5 8 L3 10 A2.5 2.5 0 0 0 6 13 L8 11 M11 8 L13 6 A2.5 2.5 0 0 0 10 3 L8 5" fill="none" stroke-width="1.6"/></svg>www.kestrel.com.sg</li>
    <li><svg viewBox="0 0 16 16"><path d="M1 6 Q8 0 15 6 L13 8 L11 6 L5 6 L3 8 Z" stroke-width="0"/><rect x="3" y="8" width="10" height="6" rx="1" stroke-width="0"/></svg>+65 9123 4567</li>
    <li><svg viewBox="0 0 16 16"><rect x="4" y="1" width="8" height="5" stroke-width="0"/><rect x="1" y="6" width="14" height="6" rx="1" stroke-width="0"/><rect x="4" y="10" width="8" height="5" fill="#fff" stroke-width="1"/></svg>+65 6123 4502</li>
  </ul>
  <div class="brand">
    <span class="brand__dot"></span>
    <span class="brand__text"><span class="brand__name">KESTREL</span><span class="brand__legal">KESTREL ASIA PACIFIC PTE LTD</span></span>
  </div>
  <p class="uen">UEN No: 200812345K</p>
  <svg class="card__bands" viewBox="0 0 540 40" aria-hidden="true">
    <rect x="0" y="28" width="540" height="12" fill="var(--band-grey)"/>
    <path d="M250 40 Q254 20 274 20 L540 20 L540 40 Z" fill="var(--orange)"/>
  </svg>
</section>

</body>
</html>
```